Fun Employee News and Engagement Portal - Tidy Hearth Company

We are looking for a clean, but fun WordPress template for an internal employee engagement website. The site will be a place we share news, fun stories and pictures. We'll provide space for our employees to post comments, etc.
We are a deep dish pizza restaurant with a rich history. I'd love to see your take on a look and feel for us! The site will be called Bim-Zee. I've posted some images and colors along with this brief description.
Focus on making the template whimsical and fun! (Extra point for focusing on the "Lettering in lights" ).
I will continue to post additional pieces of art and content examples.
Reason: Our team is continuing to review designs. We've decided to extend the timing a few more days. Good luck! Make it playful!
Reason: We need more time with our team to review these designs. We are going to extend one more time!
Reason: Still trying to get enough time to review with the Bim-Zee team!
Reason: We are continuing to evaluate designs. Thank you!
Industry/Entity Type
American Restaurant
Number of Pages Required
1 page
Look and feel
Each slider illustrates characteristics of the customer's brand and the style your logo design should communicate.

```html
<!DOCTYPE html>
<html lang="en">
<head>
<meta charset="utf-8">
<title>Bim-Zee · Tidy Hearth Company Employee Portal</title>
<link href="https://fonts.googleapis.com/css2?family=Roboto+Slab:wght@400;700&family=Open+Sans:ital,wght@0,400;0,600;1,400&display=swap" rel="stylesheet">
<style>
:root{
  --red:#e5242b;
  --red-soft:rgba(229,36,43,.88);
  --ink:#2f2f2f;
  --dark:#3b3b3d;
  --text:#6f6f6f;
  --muted:#9a9a9a;
  --page:#f4f5f7;
  --panel:#ffffff;
  --line:#e3e3e3;
  --tab:#ebebeb;
  --band:#e7e7e7;
}
*{box-sizing:border-box;margin:0;padding:0}
html,body{width:1200px;height:2503px;overflow:hidden}
body{position:relative;background:var(--page);font-family:"Open Sans",Arial,sans-serif;color:var(--text)}
.abs{position:absolute}
.slab{font-family:"Roboto Slab",Georgia,serif}

/* header */
.site-header{left:0;top:0;width:1200px;height:125px;background:#fff;border-bottom:3px solid var(--red)}
.brand{left:132px;top:34px;display:flex;align-items:center;gap:14px}
.brand-dot{width:52px;height:52px;border-radius:50%;background:var(--red)}
.brand-name{font-family:"Roboto Slab",Georgia,serif;font-weight:700;font-size:34px;color:var(--ink);letter-spacing:.5px}
.search{left:709px;top:27px;width:214px;height:28px;border:1px solid #dcdcdc;font-size:10px;color:#aaa;padding:7px 10px}
.search-btn{left:928px;top:27px;width:33px;height:28px;background:var(--red)}
.social{top:29px;width:27px;height:27px;border-radius:50%}
.nav{left:470px;top:80px;width:610px;display:flex;justify-content:space-between;font-family:"Roboto Slab",Georgia,serif;font-size:11.5px;color:var(--ink)}
.nav .active{color:var(--red)}
.nav-mark{left:487px;top:117px;width:69px;height:6px;background:var(--red)}

/* hero */
.hero{left:0;top:127px;width:1200px;height:516px;background:linear-gradient(160deg,#d9c7ae 0%,#b89a7e 40%,#6f7f8e 75%,#9bb08a 100%)}
.hero-caption{left:134px;top:527px;width:809px;height:116px;background:var(--red-soft);padding:16px 22px;color:#fff}
.hero-caption h1{font-family:"Roboto Slab",Georgia,serif;font-size:26px;font-weight:700;margin-bottom:8px}
.hero-caption p{font-size:13px;line-height:22px;opacity:.92}
.hero-arrows{left:945px;top:527px;width:123px;height:116px;background:rgba(50,50,52,.88)}

/* section tabs */
.tab{height:35px;background:var(--tab);font-family:"Roboto Slab",Georgia,serif;font-size:17px;color:var(--ink);padding:7px 14px;text-transform:uppercase}
.rule{height:3px;background:var(--red)}
.panel{background:var(--panel);border:1px solid var(--line)}
.photo{position:absolute}

.post-title{font-family:"Roboto Slab",Georgia,serif;font-weight:700;font-variant:small-caps;color:var(--ink);font-size:12.5px;line-height:21px;letter-spacing:.3px}
.small{font-size:10.5px;line-height:18px;color:var(--text)}
.story-row{left:575px;width:300px}
.story-div{left:575px;width:481px;height:1px;background:var(--line)}

.meta{display:flex;gap:26px;font-size:11px;color:var(--red);align-items:center}
.meta span{display:flex;align-items:center;gap:6px}
.btn-read{width:81px;height:27px;background:var(--red);color:#fff;font-family:"Roboto Slab",Georgia,serif;font-weight:700;font-variant:small-caps;font-size:12px;text-align:center;line-height:27px}

.emp-quote{left:925px;width:135px;font-size:10.5px;line-height:19px;font-style:italic;color:var(--text)}
.emp-quote b{display:block;font-style:normal;font-family:"Roboto Slab",Georgia,serif;font-variant:small-caps;color:var(--red);font-size:10px;text-decoration:underline}

.caption{top:1953px;width:215px;text-align:center;font-family:"Roboto Slab",Georgia,serif;font-weight:700;font-variant:small-caps;font-size:12.5px;color:var(--ink)}

.partners{left:132px;top:2015px;width:936px;height:138px;background:var(--band)}
.badge{top:2041px;width:199px;height:87px;background:#fff}

.subscribe{left:0;top:2155px;width:1200px;height:97px;background:var(--red)}
.sub-title{left:250px;top:2186px;font-family:"Roboto Slab",Georgia,serif;font-weight:700;font-variant:small-caps;font-size:24px;color:#fff;letter-spacing:.5px}
.sub-input{left:537px;top:2183px;width:403px;height:40px;background:#fff;font-size:11px;color:#777;padding:12px 14px}
.sub-btn{left:946px;top:2183px;width:122px;height:40px;background:var(--dark);color:#fff;font-family:"Roboto Slab",Georgia,serif;font-weight:700;font-size:12px;text-align:center;line-height:40px}

.foot-h{top:2272px;font-family:"Roboto Slab",Georgia,serif;font-size:14px;font-weight:700;color:var(--ink)}
.foot-p{font-size:11px;line-height:20px;color:var(--text)}
.contact-row{left:431px;display:flex;align-items:center;gap:10px;font-size:11px;color:var(--text)}
.links{left:701px;top:2303px;list-style:none;font-size:10px;color:var(--text)}
.links li{height:22px;display:flex;align-items:center;gap:8px}
.links li::before{content:"";border-left:5px solid #666;border-top:3.5px solid transparent;border-bottom:3.5px solid transparent}
.follow{top:2372px;width:31px;height:31px;border-radius:50%;border:1px solid #888}
.foot-rule{left:88px;top:2450px;width:1024px;height:1px;background:var(--line)}
.copyright{left:0;top:2470px;width:1200px;text-align:center;font-size:10px;color:var(--muted)}
</style>
</head>
<body>

<header class="site-header abs"></header>
<div class="brand abs"><span class="brand-dot"></span><span class="brand-name">Bim-Zee</span></div>
<div class="search abs">Search...</div>
<div class="search-btn abs">
  <svg width="33" height="28" viewBox="0 0 33 28"><circle cx="15.5" cy="13" r="4.5" fill="none" stroke="#fff" stroke-width="2"/><line x1="19" y1="16.5" x2="22" y2="19.5" stroke="#fff" stroke-width="2"/></svg>
</div>
<span class="social abs" style="left:973px;background:#3b5998"></span>
<span class="social abs" style="left:1000px;background:#1da1f2"></span>
<span class="social abs" style="left:1041px;background:#e02a2f"></span>
<nav class="nav abs">
  <span class="active">HOME</span><span>ABOUT US</span><span>SERVICES</span><span>STORIES</span><span>NEWS</span><span>EMPLOYEES</span><span>CONTACT US</span>
</nav>
<div class="nav-mark abs"></div>

<section class="hero abs" role="img" aria-label="Photo of four friends in sunglasses laughing and eating pizza outdoors"></section>
<div class="hero-caption abs">
  <h1>BIM-ZEE PIZZA</h1>
  <p>Accusantium doloremque laudantium, totam rem aperiam, eaque ipsa quae ab illo inventore veritatis et quasi architecto beatae vitae dicta sunt explicabo. Nemo enim ipsam voluptatem quia voluptas...</p>
</div>
<div class="hero-arrows abs">
  <svg width="123" height="116" viewBox="0 0 123 116"><polyline points="58,33 44,58 58,83" fill="none" stroke="#fff" stroke-width="2"/><polyline points="65,33 79,58 65,83" fill="none" stroke="#fff" stroke-width="2"/></svg>
</div>

<!-- Fun stories -->
<div class="tab abs" style="left:132px;top:684px;width:152px">Fun Stories</div>
<div class="rule abs" style="left:132px;top:719px;width:936px"></div>
<section class="panel abs" style="left:132px;top:738px;width:936px;height:392px"></section>
<div class="photo" style="left:145px;top:753px;width:397px;height:360px;background:linear-gradient(170deg,#b9a99a 0%,#8b6f63 50%,#2e2628 100%)" role="img" aria-label="Photo of young women laughing while eating pizza slices"></div>
<div class="abs" style="left:168px;top:1022px;font-size:11px;color:var(--red)">February 03, 2017</div>
<div class="abs post-title" style="left:168px;top:1045px;width:330px;color:#fff">It is a long established fact that a reader be distracted by the readable...</div>

<div class="story-row abs" style="top:756px"><div class="post-title">It is a long established fact that a reader be distracted by the readable</div><p class="small" style="margin-top:5px">Commodo consequat. Duis aute irure dolor in reprehendent in voluptate velit esse cillum dolore...</p></div>
<div class="photo" style="left:888px;top:754px;width:168px;height:102px;background:linear-gradient(135deg,#8a6a60,#c9a48c)" role="img" aria-label="Photo of friends sharing pizza at a table"></div>
<div class="story-div abs" style="top:870px"></div>
<div class="story-row abs" style="top:884px"><div class="post-title">It is a long established fact that a reader be distracted by the readable</div><p class="small" style="margin-top:5px">Commodo consequat. Duis aute irure dolor in reprehendent in voluptate velit esse cillum dolore...</p></div>
<div class="photo" style="left:888px;top:883px;width:168px;height:102px;background:linear-gradient(135deg,#3a3230,#9b6a48)" role="img" aria-label="Photo of hands reaching for a pizza on a wooden table"></div>
<div class="story-div abs" style="top:998px"></div>
<div class="story-row abs" style="top:1012px"><div class="post-title">It is a long established fact that a reader be distracted by the readable</div><p class="small" style="margin-top:5px">Commodo consequat. Duis aute irure dolor in reprehendent in voluptate velit esse cillum dolore...</p></div>
<div class="photo" style="left:888px;top:1011px;width:168px;height:102px;background:linear-gradient(135deg,#4a3c36,#a07860)" role="img" aria-label="Photo of a group of friends smiling at an evening party"></div>

<!-- Recent news -->
<div class="tab abs" style="left:132px;top:1162px;width:152px">Recent News</div>
<div class="rule abs" style="left:132px;top:1195px;width:663px"></div>
<section class="panel abs" style="left:132px;top:1213px;width:663px;height:471px"></section>

<div class="abs post-title" style="left:145px;top:1231px">It is a long established fact that a reader will be distracted</div>
<div class="meta abs" style="left:145px;top:1259px">
  <span><svg width="10" height="10" viewBox="0 0 10 10"><circle cx="5" cy="3" r="2.5" fill="currentColor"/><path d="M0 10a5 4 0 0 1 10 0z" fill="currentColor"/></svg>Posted by admin</span>
  <span><svg width="10" height="10" viewBox="0 0 10 10"><rect x="0" y="1.5" width="10" height="8.5" fill="currentColor"/><rect x="1.5" y="4" width="7" height="4.5" fill="#fff"/></svg>Feb 05, 2017</span>
  <span><svg width="11" height="10" viewBox="0 0 11 10"><path d="M1 1h9v6H4l-3 2.5z" fill="none" stroke="currentColor" stroke-width="1.2"/></svg>4 Comments</span>
  <span><svg width="11" height="10" viewBox="0 0 11 10"><path d="M5.5 9.5 1.2 5A2.4 2.4 0 0 1 5.5 1.8 2.4 2.4 0 0 1 9.8 5z" fill="none" stroke="currentColor" stroke-width="1.2"/></svg>13</span>
</div>
<div class="photo" style="left:145px;top:1298px;width:211px;height:137px;background:linear-gradient(135deg,#6e5a54,#c4a08a)" role="img" aria-label="Photo of friends taking a selfie with pizza"></div>
<p class="abs small" style="left:380px;top:1300px;width:390px;line-height:23px">It is a long established fact that a reader will be distracted by the readable content of a page when looking at its layout. The point of using Lorem are Ipsum is that it has a more-or-less normal distribution of letters, as opposed to usingmaking it look like readable English....</p>
<div class="btn-read abs" style="left:380px;top:1405px">Read More</div>

<div class="abs post-title" style="left:145px;top:1463px">It is a long established fact that a reader will be distracted</div>
<div class="meta abs" style="left:145px;top:1491px">
  <span><svg width="10" height="10" viewBox="0 0 10 10"><circle cx="5" cy="3" r="2.5" fill="currentColor"/><path d="M0 10a5 4 0 0 1 10 0z" fill="currentColor"/></svg>Posted by admin</span>
  <span><svg width="10" height="10" viewBox="0 0 10 10"><rect x="0" y="1.5" width="10" height="8.5" fill="currentColor"/><rect x="1.5" y="4" width="7" height="4.5" fill="#fff"/></svg>Feb 05, 2017</span>
  <span><svg width="11" height="10" viewBox="0 0 11 10"><path d="M1 1h9v6H4l-3 2.5z" fill="none" stroke="currentColor" stroke-width="1.2"/></svg>4 Comments</span>
  <span><svg width="11" height="10" viewBox="0 0 11 10"><path d="M5.5 9.5 1.2 5A2.4 2.4 0 0 1 5.5 1.8 2.4 2.4 0 0 1 9.8 5z" fill="none" stroke="currentColor" stroke-width="1.2"/></svg>13</span>
</div>
<div class="photo" style="left:145px;top:1530px;width:211px;height:137px;background:linear-gradient(135deg,#7a5a48,#c89a72)" role="img" aria-label="Photo of friends eating pizza at a restaurant table"></div>
<p class="abs small" style="left:380px;top:1532px;width:390px;line-height:23px">It is a long established fact that a reader will be distracted by the readable content of a page when looking at its layout. The point of using Lorem are Ipsum is that it has a more-or-less normal distribution of letters, as opposed to usingmaking it look like readable English....</p>
<div class="btn-read abs" style="left:380px;top:1637px">Read More</div>

<!-- Employees post -->
<div class="tab abs" style="left:811px;top:1162px;width:174px">Employees Post</div>
<div class="rule abs" style="left:811px;top:1195px;width:257px"></div>
<section class="panel abs" style="left:811px;top:1213px;width:257px;height:471px"></section>

<div class="photo" style="left:824px;top:1240px;width:86px;height:73px;background:linear-gradient(135deg,#6b7a6e,#b49a86)" role="img" aria-label="Portrait photo of an employee"></div>
<p class="emp-quote abs" style="top:1237px">"It is a long established fact distracted by the readable content of oletters..."<b>-Ned Larkin Cole</b></p>
<div class="abs" style="left:824px;top:1332px;width:232px;height:1px;background:var(--line)"></div>
<div class="photo" style="left:824px;top:1352px;width:86px;height:73px;background:linear-gradient(135deg,#cfcfcf,#6a5048)" role="img" aria-label="Portrait photo of an employee"></div>
<p class="emp-quote abs" style="top:1350px">"It is a long established fact distracted by the readable content of oletters..."<b>-Ned Larkin Cole</b></p>
<div class="abs" style="left:824px;top:1445px;width:232px;height:1px;background:var(--line)"></div>
<div class="photo" style="left:824px;top:1465px;width:86px;height:73px;background:linear-gradient(135deg,#5d6a58,#a8907a)" role="img" aria-label="Portrait photo of an employee"></div>
<p class="emp-quote abs" style="top:1462px">"It is a long established fact distracted by the readable content of oletters..."<b>-Ned Larkin Cole</b></p>
<div class="abs" style="left:824px;top:1557px;width:232px;height:1px;background:var(--line)"></div>
<div class="photo" style="left:824px;top:1577px;width:86px;height:73px;background:linear-gradient(135deg,#3fb4c0,#4a3a34)" role="img" aria-label="Portrait photo of an employee"></div>
<p class="emp-quote abs" style="top:1575px">"It is a long established fact distracted by the readable content of oletters..."<b>-Ned Larkin Cole</b></p>

<!-- Pictures -->
<div class="tab abs" style="left:132px;top:1716px;width:152px;padding-left:34px">Pictures</div>
<div class="rule abs" style="left:132px;top:1750px;width:936px"></div>
<svg class="abs" style="left:1026px;top:1727px" width="42" height="18" viewBox="0 0 42 18"><circle cx="9" cy="9" r="8" fill="#8a8a8a"/><polyline points="11,5 7,9 11,13" fill="none" stroke="#fff" stroke-width="2"/><circle cx="32" cy="9" r="8" fill="#555"/><polyline points="30,5 34,9 30,13" fill="none" stroke="#fff" stroke-width="2"/></svg>
<section class="panel abs" style="left:132px;top:1769px;width:936px;height:209px"></section>
<div class="photo" style="left:145px;top:1784px;width:215px;height:159px;background:linear-gradient(135deg,#6a4c40,#c49a7e)" role="img" aria-label="Photo of a couple sharing pizza"></div>
<div class="photo" style="left:377px;top:1784px;width:215px;height:159px;background:linear-gradient(135deg,#5a3420,#e0a24a)" role="img" aria-label="Photo of a cheesy pizza slice being lifted"></div>
<div class="photo" style="left:609px;top:1784px;width:215px;height:159px;background:linear-gradient(135deg,#2e2a2a,#8a6650)" role="img" aria-label="Photo of hands taking slices from a pizza"></div>
<div class="photo" style="left:840px;top:1784px;width:215px;height:159px;background:linear-gradient(135deg,#3a1a10,#e06a2a)" role="img" aria-label="Photo of a pizza with olives in front of an oven fire"></div>
<div class="caption abs" style="left:145px">It is a long established</div>
<div class="caption abs" style="left:377px">It is a long established</div>
<div class="caption abs" style="left:609px">It is a long established</div>
<div class="caption abs" style="left:840px">It is a long established</div>

<!-- Partners -->
<section class="partners abs"></section>
<svg class="abs" style="left:198px;top:2075px" width="14" height="20" viewBox="0 0 14 20"><polyline points="10,4 4,10 10,16" fill="none" stroke="#888" stroke-width="2.5"/></svg>
<svg class="abs" style="left:988px;top:2075px" width="14" height="20" viewBox="0 0 14 20"><polyline points="4,4 10,10 4,16" fill="none" stroke="#888" stroke-width="2.5"/></svg>
<div class="badge abs" style="left:277px"></div>
<div class="badge abs" style="left:501px"></div>
<div class="badge abs" style="left:724px"></div>

<!-- Subscribe -->
<section class="subscribe abs"></section>
<svg class="abs" style="left:134px;top:2155px" width="100" height="75" viewBox="0 0 100 75"><path d="M6 40 50 8 94 40v35H6z" fill="#c81e24"/><path d="M6 40 50 65 94 40" fill="none" stroke="#b0181e" stroke-width="3"/></svg>
<div class="sub-title abs">Subscribe Newsletter :</div>
<div class="sub-input abs">Enter Your Email Id :</div>
<div class="sub-btn abs">SUBSCRIBE</div>

<!-- Footer -->
<div class="foot-h abs" style="left:132px">ABOUT US</div>
<p class="foot-p abs" style="left:132px;top:2303px;width:230px">Commodo consequat. Duis aute irure dolor in reprehenderit in voluptate velit esse cillum dolore eu fugiat nulla pariatur. Excepteur sint...</p>
<div class="abs" style="left:132px;top:2385px;font-size:11px;color:var(--red);text-decoration:underline">Read More</div>

<div class="foot-h abs" style="left:431px">CONTACT US</div>
<div class="contact-row abs" style="top:2303px"><svg width="14" height="12" viewBox="0 0 14 12"><rect x="1" y="3" width="12" height="8" rx="2" fill="var(--red)"/><rect x="3" y="0" width="8" height="4" rx="1.5" fill="var(--red)"/></svg>(000)-121-1231 &nbsp;(Phone)</div>
<div class="contact-row abs" style="top:2329px"><svg width="14" height="12" viewBox="0 0 14 12"><rect x="1" y="4" width="12" height="6" rx="1" fill="var(--red)"/><rect x="3" y="0" width="8" height="4" fill="var(--red)"/><rect x="3" y="9" width="8" height="3" fill="#fff" stroke="var(--red)"/></svg>(000)-121-1231 &nbsp;(Fax)</div>
<div class="contact-row abs" style="top:2356px"><svg width="14" height="12" viewBox="0 0 14 12"><rect x="0" y="1" width="14" height="10" fill="var(--red)"/><polyline points="0,1 7,7 14,1" fill="none" stroke="#fff" stroke-width="1.2"/></svg><span style="text-decoration:underline">info@bimzee-team.com</span></div>
<div class="contact-row abs" style="top:2383px;align-items:flex-start"><svg width="14" height="14" viewBox="0 0 14 14"><path d="M7 14S2 8 2 5a5 5 0 0 1 10 0c0 3-5 9-5 9z" fill="var(--red)"/><circle cx="7" cy="5" r="2" fill="#fff"/></svg><span style="line-height:15px"># lorem Ipsum Dummy text<br>Lorem Ipsum</span></div>

<div class="foot-h abs" style="left:701px">QUICK LINKS</div>
<ul class="links abs">
  <li>ABOUT US</li><li>SERVICES</li><li>STORIES</li><li>NEWS</li><li>EMPLOYEES</li><li>CONTACT US</li>
</ul>

<div class="foot-h abs" style="left:880px">FOLLOW US</div>
<p class="foot-p abs" style="left:880px;top:2303px;width:200px;line-height:18px">It is a long established fact that a reader will be distracted by the readable content of a page when looking at its layout.</p>
<span class="follow abs" style="left:874px"></span>
<span class="follow abs" style="left:918px"></span>
<span class="follow abs" style="left:963px"></span>
<span class="follow abs" style="left:1008px"></span>

<div class="foot-rule abs"></div>
<div class="copyright abs">© COPY RIGHT2016 BIM-ZEE . ALL RIGHTS RESERVED</div>

</body>
</html>
```